Company identity deisgn should support 2 languages

I would like to get our company identity design
This includes the following only
Business Cards 2 languages Arabic and English
Email signature
Letterhead
Linkedin profile images
Attached is the logo in Ai format

Requirements
Must have
• For business card
Must have
Name and Adrees in arabic
Name and Address in english
You might use both side of the card
Should not have
• Any pictures other than the logo

```html
<!DOCTYPE html>
<html lang="en">
<head>
<meta charset="utf-8">
<title>Meridian Data Systems – Stationery</title>
<link href="https://fonts.googleapis.com/css2?family=Roboto:wght@400;500;700&family=Noto+Sans+Arabic:wght@400;500&display=swap" rel="stylesheet">
<style>
  :root{
    --brand-blue:#1a6db4;
    --ink:#4a4a4a;
    --ink-soft:#6b6b6b;
    --paper:#ffffff;
    --paper-tint:#f7f8fa;
    --stage-top:#eeedeb;
    --stage-bottom:#dcdcdc;
    --faint-blue:#e3eaf5;
  }
  *{box-sizing:border-box;margin:0;padding:0}
  html,body{width:1200px;height:2164px;overflow:hidden}
  body{font-family:"Roboto",Arial,sans-serif;color:var(--ink);background:var(--stage-bottom);position:relative}
  .ar{font-family:"Noto Sans Arabic","Roboto",sans-serif}

  .cards-stage{position:absolute;left:0;top:0;width:1200px;height:925px;background:var(--stage-top)}
  .card{position:absolute;width:520px;height:297px;box-shadow:0 10px 24px rgba(0,0,0,.14)}
  .card--back{left:60px;top:314px;background:var(--brand-blue)}
  .card--front{left:620px;top:314px;background:var(--paper)}

  .brand{display:flex;align-items:center;gap:10px;font-weight:500;letter-spacing:.06em;text-transform:uppercase;white-space:nowrap}
  .brand__dot{border-radius:50%;flex:none}
  .card--back .brand{position:absolute;left:50%;top:50%;transform:translate(-50%,-50%);color:#fff;font-size:24px}
  .card--back .brand__dot{width:34px;height:34px;background:#fff}
  .card--front .brand{position:absolute;right:30px;top:30px;color:var(--brand-blue);font-size:15px}
  .card--front .brand__dot{width:20px;height:20px;background:var(--brand-blue)}

  .person__name{color:var(--brand-blue);font-weight:700}
  .person__title{font-weight:500;color:var(--ink-soft)}
  .contact-line{display:flex;align-items:center;gap:6px}
  .contact-line svg{flex:none;fill:var(--brand-blue)}

  .card--front .person{position:absolute;left:30px;top:128px;font-size:11.5px;line-height:1.45}
  .card--front .person__name{font-size:16px}
  .card--front .person__title{font-size:12px;margin-bottom:6px}
  .card--front .office{position:absolute;right:30px;bottom:34px;text-align:right;font-size:11.5px;line-height:1.45}

  .letter{position:absolute;top:988px;width:410px;height:575px;background:var(--paper-tint);box-shadow:0 8px 22px rgba(0,0,0,.14);padding:46px 37px 0 38px;overflow:hidden;font-size:6.6px;line-height:1.7}
  .letter--left{left:165px}
  .letter--right{left:614px}
  .letter .brand{color:var(--brand-blue);font-size:10px;gap:7px}
  .letter .brand__dot{width:22px;height:22px;background:var(--brand-blue)}
  .letter__greeting{margin-top:64px;margin-bottom:10px}
  .letter__body p{margin-bottom:11px;text-align:justify}
  .letter__closing{margin-top:14px}
  .letter__signature{display:block;width:48px;height:40px;margin-top:14px;background:#cfd3d8;border-radius:3px}
  .letter__footer{position:absolute;left:38px;bottom:30px;font-size:8px;line-height:1.55}
  .letter__footer svg{width:8px;height:8px}
  .letter__deco{position:absolute;right:-30px;bottom:-40px;width:190px;height:190px;border-radius:50%;background:var(--faint-blue);opacity:.7}

  .signature{position:absolute;left:162px;top:1718px;width:880px;height:298px;background:var(--paper);box-shadow:0 8px 20px rgba(0,0,0,.22);overflow:hidden}
  .signature__deco{position:absolute;right:-40px;top:-60px;width:300px;height:300px;border-radius:50%;background:var(--faint-blue);opacity:.8}
  .signature .person{position:absolute;left:58px;top:48px;font-size:21px;line-height:1.3}
  .signature .person__name{font-size:27px}
  .signature .person__title{font-size:21px;margin-bottom:18px}
  .signature .contact-line svg{width:20px;height:20px}
  .signature .contact-list{margin-top:12px;line-height:1.25}
  .signature .office{position:absolute;right:58px;bottom:44px;text-align:right;font-size:21px;line-height:1.3}
</style>
</head>
<body>
<svg width="0" height="0" style="position:absolute" aria-hidden="true">
  <defs>
    <symbol id="icon-phone" viewBox="0 0 24 24"><path d="M6.6 10.8a15 15 0 0 0 6.6 6.6l2.2-2.2a1 1 0 0 1 1-.25 11.4 11.4 0 0 0 3.6.57 1 1 0 0 1 1 1V20a1 1 0 0 1-1 1A17 17 0 0 1 3 4a1 1 0 0 1 1-1h3.5a1 1 0 0 1 1 1c0 1.25.2 2.45.57 3.57a1 1 0 0 1-.25 1z"/></symbol>
    <symbol id="icon-mail" viewBox="0 0 24 24"><path d="M2 5h20v14H2z M3.5 6.5 12 13l8.5-6.5" stroke="#fff" stroke-width="1.4"/></symbol>
    <symbol id="icon-globe" viewBox="0 0 24 24"><circle cx="12" cy="12" r="10"/><path d="M2 12h20M12 2c3 3 3 17 0 20M12 2c-3 3-3 17 0 20" fill="none" stroke="#fff" stroke-width="1.3"/></symbol>
  </defs>
</svg>

<section class="cards-stage">
  <div class="card card--back">
    <div class="brand"><span class="brand__dot"></span>Meridian Data Systems</div>
  </div>
  <div class="card card--front">
    <div class="brand"><span class="brand__dot"></span>Meridian Data Systems</div>
    <div class="person">
      <div class="person__name">KARIM HADDAD <span class="ar">(كريم حداد)</span></div>
      <div class="person__title">Managing Director</div>
      <div class="ar" dir="rtl" style="text-align:left">42 سيدار ريدج، كاملوبس</div>
      <div class="ar" dir="rtl" style="text-align:left">بي سي كندا V2C 1A7</div>
      <div class="contact-line"><svg width="11" height="11"><use href="#icon-phone"/></svg>604.555.0182</div>
      <div class="contact-line"><svg width="11" height="11"><use href="#icon-mail"/></svg>info@meridianmail.com</div>
      <div class="contact-line"><svg width="11" height="11"><use href="#icon-globe"/></svg>www.meridianweb.com</div>
    </div>
    <div class="office">42 Cedar Ridge Ln, Kamloops<br>B.C. Canada V2C 1A7</div>
  </div>
</section>

<article class="letter letter--left">
  <div class="brand"><span class="brand__dot"></span>Meridian Data Systems</div>
  <p class="letter__greeting">Dear customer,</p>
  <div class="letter__body">
    <p>We appreciate your continued trust in our team. This letter outlines the next steps for your project, including timelines, deliverables and review meetings. Please contact our office with any questions, and we will respond promptly with the details you need to proceed.</p>
    <p>We appreciate your continued trust in our team. This letter outlines the next steps for your project, including timelines, deliverables and review meetings. Please contact our office with any questions, and we will respond promptly with the details you need to proceed.</p>
    <p>We appreciate your continued trust in our team. This letter outlines the next steps for your project, including timelines, deliverables and review meetings. Please contact our office with any questions, and we will respond promptly with the details you need to proceed.</p>
  </div>
  <p class="letter__closing">Yours Sincerely,</p>
  <span class="letter__signature" role="img" aria-label="Handwritten signature"></span>
  <div class="letter__deco"></div>
  <div class="letter__footer">
    <div>42 Cedar Ridge Ln, Kamloops</div>
    <div>B.C. Canada V2C 1A7</div>
    <div class="contact-line"><svg><use href="#icon-phone"/></svg>604.555.0182</div>
    <div class="contact-line"><svg><use href="#icon-mail"/></svg>info@meridianmail.com</div>
    <div class="contact-line"><svg><use href="#icon-globe"/></svg>www.meridianweb.com</div>
  </div>
</article>

<article class="letter letter--right">
  <div class="brand"><span class="brand__dot"></span>Meridian Data Systems</div>
  <p class="letter__greeting">Dear customer,</p>
  <div class="letter__body">
    <p>We appreciate your continued trust in our team. This letter outlines the next steps for your project, including timelines, deliverables and review meetings. Please contact our office with any questions, and we will respond promptly with the details you need to proceed.</p>
    <p>We appreciate your continued trust in our team. This letter outlines the next steps for your project, including timelines, deliverables and review meetings. Please contact our office with any questions, and we will respond promptly with the details you need to proceed.</p>
    <p>We appreciate your continued trust in our team. This letter outlines the next steps for your project, including timelines, deliverables and review meetings. Please contact our office with any questions, and we will respond promptly with the details you need to proceed.</p>
  </div>
  <p class="letter__closing">Yours Sincerely,</p>
  <span class="letter__signature" role="img" aria-label="Handwritten signature"></span>
  <div class="letter__deco"></div>
  <div class="letter__footer">
    <div>42 Cedar Ridge Ln, Kamloops</div>
    <div>B.C. Canada V2C 1A7</div>
    <div class="contact-line"><svg><use href="#icon-phone"/></svg>604.555.0182</div>
    <div class="contact-line"><svg><use href="#icon-mail"/></svg>info@meridianmail.com</div>
    <div class="contact-line"><svg><use href="#icon-globe"/></svg>www.meridianweb.com</div>
  </div>
</article>

<section class="signature">
  <div class="signature__deco"></div>
  <div class="person">
    <div class="person__name">KARIM HADDAD <span class="ar" style="font-weight:500">(كريم حداد)</span></div>
    <div class="person__title">Managing Director</div>
    <div class="ar" dir="rtl" style="text-align:left">42 سيدار ريدج، كاملوبس</div>
    <div class="ar" dir="rtl" style="text-align:left">بي سي كندا V2C 1A7</div>
    <div class="contact-list">
      <div class="contact-line"><svg><use href="#icon-phone"/></svg>604.555.0182</div>
      <div class="contact-line"><svg><use href="#icon-mail"/></svg>info@meridianmail.com</div>
      <div class="contact-line"><svg><use href="#icon-globe"/></svg>www.meridianweb.com</div>
    </div>
  </div>
  <div class="office">42 Cedar Ridge Ln, Kamloops<br>B.C. Canada V2C 1A7</div>
</section>
</body>
</html>
```